Business Card Design

Business Card for professional consulting firm working with large financial institutions.

Target Market(s)

Executive buyers

Industry/Entity Type

Banking

Contact Information for Business Card

Mild creativity wanted. Not boring, but do elaborate artwork.

Font styles to use
Serif
Sans Serif

Colors

Designer to choose colors to be used in the design.

Requirements
Must have
• Standard business card features - company name, individual name, telephone, website, email, locations.
Nice to have
• Two colors
Should not have
• too many colors, fancy printing, cartoons.

```html
<!DOCTYPE html>
<html lang="en">
<head>
<meta charset="utf-8">
<title>k7advisors – Business Card</title>
<link rel="stylesheet" href="https://fonts.googleapis.com/css2?family=Noto+Serif&family=Roboto:wght@400;500&display=swap">
<style>
  :root {
    --ink: #0b0b0b;
    --paper: #f2f2f2;
    --swoosh: #b9b9b9;
    --text-grey: #6a6a6a;
    --wordmark-grey: #555555;
    --white: #ffffff;
    --backdrop: #d8d3cb;
  }
  * { margin: 0; padding: 0; box-sizing: border-box; }
  html, body { width: 1200px; height: 950px; overflow: hidden; }
  body { background: var(--backdrop); position: relative; }

  .card {
    position: absolute;
    width: 620px;
    height: 354px;
    overflow: hidden;
    box-shadow: 0 6px 18px rgba(0,0,0,0.25);
  }

  /* Front */
  .card--front { left: 60px; top: 110px; background: var(--paper); }
  .front__shape { position: absolute; inset: 0; width: 100%; height: 100%; }
  .front__person {
    position: absolute; right: 34px; top: 34px; text-align: right;
    font-family: "Roboto", sans-serif; color: var(--white);
  }
  .person__name { font-size: 21px; font-weight: 500; letter-spacing: 0.5px; }
  .person__title { font-size: 14px; font-weight: 400; margin-top: 4px; letter-spacing: 0.5px; }

  .front__wordmark {
    position: absolute; left: 58px; top: 112px;
    font-family: "Noto Serif", serif; font-size: 44px; color: var(--wordmark-grey);
  }
  .front__contact {
    position: absolute; left: 60px; top: 192px;
    font-family: "Roboto", sans-serif; font-size: 14px; line-height: 21px; color: var(--text-grey);
  }
  .contact__line { display: flex; align-items: center; gap: 8px; }
  .contact__icon { width: 12px; height: 12px; flex: none; }
  .contact__address { margin-bottom: 4px; }

  /* Back */
  .card--back {
    left: 520px; top: 500px; background: var(--ink);
    display: flex; align-items: center; justify-content: center;
  }
  .back__wordmark {
    font-family: "Noto Serif", serif; font-size: 68px; color: var(--white); letter-spacing: 1px;
  }
</style>
</head>
<body>

<section class="card card--front" aria-label="Business card front">
  <svg class="front__shape" viewBox="0 0 620 354" aria-hidden="true">
    <path d="M360 0 C470 40 580 170 612 354 L596 354 C560 175 455 50 345 0 Z" fill="var(--swoosh)"/>
    <path d="M345 0 L620 0 L620 354 L596 354 C560 175 455 50 345 0 Z" fill="var(--ink)"/>
  </svg>

  <div class="front__person">
    <p class="person__name">DANIEL HART</p>
    <p class="person__title">CEO/FOUNDER</p>
  </div>

  <p class="front__wordmark">k7advisors</p>

  <div class="front__contact">
    <div class="contact__address">
      <p>k7advisors</p>
      <p>1420 Alder Court</p>
      <p>Juneau, Alaska 99801</p>
    </div>
    <p class="contact__line">
      <svg class="contact__icon" viewBox="0 0 12 12" aria-hidden="true"><path d="M2.5 1 L4.5 1 L5.5 3.5 L4 4.6 C4.6 6 6 7.4 7.4 8 L8.5 6.5 L11 7.5 L11 9.5 C11 10.4 10.3 11 9.5 11 C5 10.7 1.3 7 1 2.5 C1 1.7 1.6 1 2.5 1 Z" fill="var(--ink)"/></svg>
      555 210 4837
    </p>
    <p class="contact__line">
      <svg class="contact__icon" viewBox="0 0 12 12" aria-hidden="true"><rect x="0.5" y="2" width="11" height="8" fill="var(--ink)"/><path d="M0.5 2 L6 6.5 L11.5 2" stroke="var(--paper)" fill="none"/></svg>
      info@k7advisors.com
    </p>
    <p class="contact__line">
      <svg class="contact__icon" viewBox="0 0 12 12" aria-hidden="true"><circle cx="6" cy="6" r="5.5" fill="var(--ink)"/><path d="M0.5 6 H11.5 M6 0.5 C3 3.5 3 8.5 6 11.5 M6 0.5 C9 3.5 9 8.5 6 11.5" stroke="var(--paper)" stroke-width="0.8" fill="none"/></svg>
      www.k7advisors.com
    </p>
  </div>
</section>

<section class="card card--back" aria-label="Business card back">
  <p class="back__wordmark">k7advisors</p>
</section>

</body>
</html>
```